Venture Capital Investment Firm

We are looking to overhaul our existing website (substantially), with only using the same logos (which we can provide).
We are an investment firm that focuses on making loans to late stage technology companies. Our site should ultimately look like other venture capital firms, and look modern and fresh. We have an existing website www.norvellhub.com which this will be replacing, although we will be using a lot of the existing written content, and potentially the numbers of pages we will need, we are not wed to anything else. Please feel free to shoot any questions at any time and thank you in advance for your help!
Websites we like as examples:
https://www.tesmarkfund.com/
https://www.brindlewoodpartners.com/
Target Market(s)
Potential investors who will invest in our firm, as well as potentially companies that are looking to borrow money from us.
Coding
Coded - Design and coding required
Number of Pages Required
5+ page
Colors
Designer to choose colors to be used in the design.
Look and feel

```html
<!DOCTYPE html>
<html lang="en">
<head>
<meta charset="utf-8">
<title>Norvell Hub — About Us</title>
<link rel="stylesheet" href="https://fonts.googleapis.com/css2?family=Jost:wght@400;500;600&family=Questrial&display=swap">
<style>
:root{
  --navy:#05062e;
  --ink:#0a0b3a;
  --text:#444;
  --footer:#4a4a4a;
  --white:#fff;
}
*{margin:0;padding:0;box-sizing:border-box}
html,body{width:771px;height:1200px;overflow:hidden;background:var(--white)}
.page{position:relative;width:771px;height:1200px;overflow:hidden;font-family:"Questrial",sans-serif;color:var(--text)}
.abs{position:absolute}

/* hero */
.hero{left:0;top:0;width:771px;height:376px;
  background:linear-gradient(180deg,var(--navy) 0%,#0d0d33 18%,#3a3448 45%,#7b6257 70%,#4e3d36 100%)}
.hero-photo{left:0;top:60px;width:771px;height:316px;
  background:radial-gradient(ellipse at 75% 55%,rgba(190,160,140,.55),rgba(0,0,0,0) 60%),
             linear-gradient(90deg,rgba(20,20,30,.6),rgba(0,0,0,0) 50%)}
.brand{left:30px;top:14px;display:flex;align-items:center;gap:7px;color:var(--white);font-family:"Jost",sans-serif;font-weight:500}
.brand-mark{width:22px;height:22px;border-radius:50%;background:var(--white)}
.brand-name{font-size:16px;letter-spacing:1px;line-height:1}
.nav{top:19px;left:332px;display:flex;align-items:center;font-family:"Jost",sans-serif;font-size:8px;letter-spacing:1px;color:var(--white)}
.nav a{color:inherit;text-decoration:none;margin-right:26px}
.nav .cta{margin:0 0 0 2px;background:var(--white);color:var(--ink);padding:5px 8px}
.hero-band{left:134px;top:125px;width:503px;height:31px;background:rgba(190,190,205,.55);
  font-family:"Jost",sans-serif;font-weight:600;font-size:20px;color:var(--white);text-align:center;line-height:31px;text-shadow:1px 1px 2px rgba(0,0,0,.5)}
.hero-title{right:166px;top:214px;font-family:"Jost",sans-serif;font-weight:600;font-size:20px;color:var(--white);text-shadow:1px 1px 2px rgba(0,0,0,.6)}
.hero-copy{right:381px;top:263px;width:320px;text-align:right;font-family:"Jost",sans-serif;font-weight:600;font-size:14.5px;line-height:17px;letter-spacing:1px;color:var(--white);text-shadow:1px 1px 2px rgba(0,0,0,.6)}

/* content */
.section-title{left:0;width:771px;text-align:center;font-family:"Jost",sans-serif;font-weight:600;font-size:22px;color:var(--ink)}
.section-sub{left:0;width:771px;text-align:center;font-family:"Jost",sans-serif;font-weight:500;font-size:13px;letter-spacing:2.3px;color:#3a3a3a}
.body-copy{left:30px;width:711px;text-align:center;font-size:8.5px;line-height:10.8px;color:var(--text)}
.stat{width:95px;height:95px;border:1.5px solid var(--ink);border-radius:50%;display:flex;align-items:center;justify-content:center;
  font-family:"Jost",sans-serif;font-weight:600;font-size:24px;color:var(--ink)}
.stat-label{width:170px;text-align:center;font-family:"Jost",sans-serif;font-weight:500;font-size:10px;line-height:11px;color:var(--ink)}

/* footer */
.footer{left:0;top:924px;width:771px;height:209px;background:var(--footer);color:var(--white)}
.f-head{font-family:"Jost",sans-serif;font-weight:500;font-size:11px}
.f-text{font-size:8.5px;line-height:11px}
.map{left:445px;top:957px;width:276px;height:143px;background:linear-gradient(135deg,#e9e5dc 0%,#e9e5dc 38%,#a9d2f2 42%,#a9d2f2 100%)}
.bottom{left:0;top:1133px;width:771px;height:67px;background:var(--navy);color:var(--white)}
.bottom-nav{left:352px;top:1147px;width:369px;display:flex;justify-content:space-between;font-family:"Jost",sans-serif;font-size:8px;letter-spacing:.8px;color:var(--white)}
.legal{left:0;width:771px;top:1174px;text-align:center;font-size:8.5px;color:var(--white);text-decoration:underline}
</style>
</head>
<body>
<div class="page">
  <div class="abs hero"></div>
  <div class="abs hero-photo" role="img" aria-label="Photo of a light bulb lying on a wooden table"></div>
  <div class="abs brand"><span class="brand-mark"></span><span class="brand-name">NORVELL HUB</span></div>
  <nav class="abs nav"><a>HOME</a><a>STRATEGY</a><a>ABOUT US</a><a>TEAM</a><a>NEWS</a><a>CONTACT</a><a class="cta">INVESTORS</a></nav>
  <div class="abs hero-band">ABOUT US</div>
  <div class="abs hero-title">Lorem ipsum dolor sit</div>
  <p class="abs hero-copy">Lorem ipsum dolor sit amet, consectetur adipiscing elit. Phasellus orci nulla, convallis eget vulputate ut, pulvinar ut lectus.</p>

  <h1 class="abs section-title" style="top:403px">NORVELL HUB STARTED WITH A BIG IDEA</h1>
  <h2 class="abs section-sub" style="top:436px">FINANCE PROVEN INNOVATION WITH A DIFFERENT APPROACH</h2>
  <p class="abs body-copy" style="top:466px">Norvell Hub is a private investment firm unique in its dual focus on life science and technology credit opportunities. Our ambidextrous approach to investing reflects a broad<br>recognition and appreciation for the critical role intellectual property plays in the successful commercialization of products. We apply our extensive industry expertise<br>to assess the revenue visibility created by these assets and offer a range of creative financing solutions.</p>
  <p class="abs body-copy" style="top:510px">A pioneer in providing life science structured credit beginning in 2004, the Norvell Hub team was the first to introduce flexible structured credit<br>to the technology sector in 2014. Our team was also early to recognize the potential of "non-core" assets beyond drug<br>royalties, acquiring over $300M of branded generics offering predictable cash flows from large pharmaceutical firms<br>and partnering with entrepreneurial teams to successfully manage these brands.</p>

  <h2 class="abs section-title" style="top:609px">OUR EXPERIENCE</h2>
  <div class="abs stat" style="left:165px;top:666px">$1.2 B</div>
  <div class="abs stat" style="left:334px;top:666px">40+</div>
  <div class="abs stat" style="left:502px;top:666px">12+</div>
  <div class="abs stat-label" style="left:127px;top:777px">OVER $1.2B INVESTED<br>BY OUR PARTNERS</div>
  <div class="abs stat-label" style="left:296px;top:777px">40+ LIFE SCIENCE AND<br>TECHNOLOGY INVESTMENTS</div>
  <div class="abs stat-label" style="left:466px;top:766px">OVER A DECADE<br>INNOVATING<br>FINANCING STRUCTURES</div>
  <p class="abs body-copy" style="top:817px">We bring over 40 years of collective experience to our investments, including over $1.2B invested within structured credit,<br>milestones and royalties, and the acquisition of legacy assets from some of the world's largest and most well respected pharmaceutical companies.<br>In addition, members of the Norvell Hub team have played senior roles in executing over $75B of M&amp;A, equity,<br>and debt financings in the life science and technology sectors.</p>
  <p class="abs body-copy" style="top:871px">Along the way we've built strong relationships and friendships with entrepreneurial management teams, investors, and executives who acquire and<br>commercialize innovative products and technologies. These relationships offer Norvell Hub unique insight into the industries, companies, and products where we invest.</p>

  <footer class="abs footer"></footer>
  <div class="abs f-head" style="left:48px;top:955px;color:#fff">GENERAL INQUIRIES:</div>
  <div class="abs f-text" style="left:48px;top:974px;color:#fff">inquiries@norvellhub.com</div>
  <div class="abs f-head" style="left:48px;top:994px;color:#fff">MEDIA INQUIRIES:</div>
  <div class="abs f-text" style="left:48px;top:1012px;color:#fff">media@norvellhub.com</div>
  <div class="abs f-head" style="left:48px;top:1033px;color:#fff">TRANSACTION OPPORTUNITIES</div>
  <div class="abs f-text" style="left:48px;top:1052px;color:#fff">invopps@norvellhub.com</div>
  <div class="abs f-head" style="left:48px;top:1072px;color:#fff">CAREERS</div>
  <div class="abs f-text" style="left:48px;top:1091px;color:#fff">career@norvellhub.com</div>
  <div class="abs f-head" style="left:276px;top:955px;color:#fff">ADDRESS:</div>
  <div class="abs f-text" style="left:276px;top:974px;color:#fff">2250 LARKSPUR AVENUE #310<br>SAN FRANCISCO, CA 94107</div>
  <div class="abs map" role="img" aria-label="Street map showing the office location in San Francisco"></div>

  <div class="abs bottom"></div>
  <div class="abs f-text" style="left:48px;top:1147px;color:#fff">NORVELL HUB, SAN FRANCISCO<br>© 2015 Norvell Hub Investment Partners LLC. All Rights Reserved.</div>
  <nav class="abs bottom-nav"><span>HOME</span><span>STRATEGY</span><span>ABOUT US</span><span>TEAM</span><span>NEWS</span><span>CONTACT</span><span>INVESTORS</span></nav>
  <div class="abs legal">Legal Disclaimer</div>
</div>
</body>
</html>
```